Verodex business card

Business card for sustainable investment company called "Verodex". Verodex is an exchange platform selling carbon credits between buyers and sellers. Carbon Credits are an environmental commodity for reducing global carbon emissions.

the card should obviously have our logo and the theme should be sustainability/environment mixed with a trading platform.

Contact Information for Business Card

Logo, Name, Title, Phone, Email

Colors
0054AA
0677BA
7BADD7
CADEEF
E8F1F8
0094D4
00A9DD
6FCCEA
C7EBF8
E9F6FB
00AB8E
00BBA5
67D7C9
C6EFE9
E9F9F6
59FF00
82FF00
B8FF75
E3FFCB
F4FFEA

```html
<!DOCTYPE html>
<html lang="en">
<head>
<meta charset="utf-8">
<title>Verodex business card</title>
<link href="https://fonts.googleapis.com/css2?family=Open+Sans:wght@400;600;700;800&display=swap" rel="stylesheet">
<style>
  :root {
    --page: #e9edf2;
    --navy: #142b52;
    --navy-deep: #0d1d38;
    --ink: #ffffff;
    --sky: #5bb8e0;
    --sky-light: #7bcbeb;
    --tab-a: #4fa9d9;
    --tab-b: #2f7fb8;
    --emboss: #0c172b;
  }
  * { box-sizing: border-box; margin: 0; padding: 0; }
  html, body { width: 1200px; height: 780px; overflow: hidden; }
  body {
    background: var(--page);
    font-family: "Open Sans", Arial, sans-serif;
    position: relative;
  }
  .card {
    position: absolute;
    top: 241px;
    width: 520px;
    height: 297px;
    border-radius: 18px;
    background: var(--navy);
    overflow: hidden;
    box-shadow: 0 10px 26px rgba(13, 29, 56, 0.28);
  }
  .card--front { left: 60px; }
  .card--back { left: 620px; }

  .brand {
    position: absolute;
    display: flex;
    align-items: center;
    gap: 12px;
  }
  .brand__mark { width: 26px; height: 26px; border-radius: 3px; }
  .brand__name {
    font-weight: 800;
    letter-spacing: 0.5px;
    text-transform: uppercase;
    line-height: 1;
  }
  .card--front .brand { left: 28px; top: 26px; }
  .card--front .brand__mark { background: var(--tab-a); }
  .card--front .brand__name { font-size: 30px; color: var(--ink); }

  .card--back .brand { left: 50%; top: 50%; transform: translate(-50%, -50%); gap: 16px; }
  .card--back .brand__mark { width: 38px; height: 38px; background: var(--emboss); }
  .card--back .brand__name { font-size: 44px; color: var(--emboss); }

  .divider {
    position: absolute;
    left: 92px;
    top: 152px;
    width: 346px;
    height: 1.5px;
    background: var(--ink);
  }
  .person {
    position: absolute;
    right: 82px;
    top: 96px;
    text-align: right;
  }
  .person__name {
    font-size: 25px;
    font-weight: 700;
    color: var(--sky);
    line-height: 1.1;
  }
  .person__title {
    font-size: 14px;
    font-weight: 600;
    color: var(--ink);
    letter-spacing: 0.3px;
    margin-top: 1px;
  }
  .address {
    position: absolute;
    right: 82px;
    top: 166px;
    text-align: right;
    font-size: 15px;
    color: var(--ink);
    line-height: 1.45;
  }
  .contact {
    position: absolute;
    left: 26px;
    top: 196px;
    list-style: none;
  }
  .contact__item {
    display: flex;
    align-items: center;
    gap: 8px;
    font-size: 12.5px;
    color: var(--ink);
    line-height: 1;
    margin-bottom: 9px;
  }
  .contact__icon { width: 13px; height: 13px; flex: none; }
  .edge-tab {
    position: absolute;
    right: 0;
    top: 140px;
    width: 16px;
    height: 26px;
    background: linear-gradient(180deg, var(--sky-light), var(--tab-a));
  }
  .edge-tab--lower {
    top: 166px;
    width: 10px;
    height: 14px;
    background: var(--tab-b);
  }
</style>
</head>
<body>
  <section class="card card--front" aria-label="Card front">
    <div class="brand">
      <span class="brand__mark"></span>
      <span class="brand__name">Verodex</span>
    </div>

    <div class="person">
      <p class="person__name">Lenka Marova</p>
      <p class="person__title">Managing Director</p>
    </div>
    <div class="divider"></div>
    <address class="address">
      1840 Meadowbrook Ave. Suite 310<br>
      Denton, TX 76201
    </address>

    <ul class="contact">
      <li class="contact__item">
        <svg class="contact__icon" viewBox="0 0 24 24" aria-hidden="true"><path fill="#5bb8e0" d="M6.6 10.8a15.1 15.1 0 0 0 6.6 6.6l2.2-2.2a1 1 0 0 1 1-.25 11.4 11.4 0 0 0 3.6.57 1 1 0 0 1 1 1V20a1 1 0 0 1-1 1A17 17 0 0 1 3 4a1 1 0 0 1 1-1h3.5a1 1 0 0 1 1 1c0 1.25.2 2.45.57 3.57a1 1 0 0 1-.25 1z"/></svg>
        (555) 214-0386
      </li>
      <li class="contact__item">
        <svg class="contact__icon" viewBox="0 0 24 24" aria-hidden="true"><rect x="2" y="5" width="20" height="14" rx="2" fill="#5bb8e0"/><path d="M3 6l9 7 9-7" fill="none" stroke="#142b52" stroke-width="2"/></svg>
        info@verodex.com
      </li>
      <li class="contact__item">
        <svg class="contact__icon" viewBox="0 0 24 24" aria-hidden="true"><circle cx="12" cy="12" r="10" fill="#5bb8e0"/><path d="M2 12h20M12 2c3 3 3 17 0 20M12 2c-3 3-3 17 0 20" fill="none" stroke="#142b52" stroke-width="1.6"/></svg>
        www.verodex.com
      </li>
    </ul>

    <span class="edge-tab"></span>
    <span class="edge-tab edge-tab--lower"></span>
  </section>

  <section class="card card--back" aria-label="Card back">
    <div class="brand">
      <span class="brand__mark"></span>
      <span class="brand__name">Verodex</span>
    </div>
  </section>
</body>
</html>
```